Business Card Design for Flood Rescue 360 - Property Restoration Professionals

I need a business card designed for Flood Rescue 360. We are a full-service property restoration solution. Providing water, fire, smoke & storm restoration as well as mold remediation and full remodel or reconstruction to homes and businesses across Dallas-Fort Worth, TX.
Target Market(s)
home and business owners with insurance covered property damage from water, fire or storm related damage
Industry/Entity Type
property restoration
Contact Information for Business Card
Marcus Pelley General Manager Cell: 214-555-0193 Office: 469-555-0148 email: Marcus@FloodRescue360.example services: Water, Fire, Mold, Reconstruction Tagline: Urgency for Your Water Emergency!
Look and feel
Each slider illustrates characteristics of the customer's brand and the style your logo design should communicate.

```html
<!DOCTYPE html>
<html lang="en">
<head>
<meta charset="utf-8">
<title>Flood Rescue 360 – Business Card</title>
<link href="https://fonts.googleapis.com/css2?family=Montserrat:wght@400;500;800;900&display=swap" rel="stylesheet">
<style>
  :root {
    --stage: #4a4a4a;
    --card: #161616;
    --card-back: #141414;
    --accent: #00b2e8;
    --ink: #ffffff;
    --muted: #8a8a8a;
    --emboss: #9a9a9a;
  }
  * { box-sizing: border-box; margin: 0; padding: 0; }
  html, body {
    width: 1200px; height: 801px; overflow: hidden;
    background: var(--stage);
    font-family: "Montserrat", sans-serif;
  }
  .stage {
    position: relative; width: 1200px; height: 801px;
    display: flex; align-items: center; justify-content: center; gap: 40px;
  }
  .card {
    position: relative; width: 540px; height: 309px;
    background: var(--card);
    border-bottom: 3px solid var(--accent);
    box-shadow: 0 18px 40px rgba(0,0,0,.45);
    overflow: hidden;
  }
  .card--back { background: var(--card-back); }

  /* front: brand */
  .brand {
    position: absolute; top: 26px; right: 28px;
    display: flex; align-items: center; gap: 12px;
  }
  .brand__name {
    color: var(--accent); font-weight: 900; font-size: 27px;
    line-height: .95; text-transform: uppercase; text-align: right;
  }
  .brand__dot {
    width: 44px; height: 44px; border-radius: 50%;
    border: 4px solid var(--accent);
  }

  /* front: services */
  .services {
    position: absolute; right: 28px; top: 128px; text-align: right;
  }
  .services__title {
    color: var(--accent); font-weight: 900; font-size: 19px;
    text-transform: uppercase; letter-spacing: .5px; margin-bottom: 4px;
  }
  .services__list { list-style: none; }
  .services__item {
    color: var(--ink); font-size: 13px; line-height: 1.5;
    display: flex; justify-content: flex-end; align-items: center; gap: 6px;
  }
  .services__item::after {
    content: ""; width: 7px; height: 7px; border-radius: 50%;
    border: 1.5px solid var(--accent);
  }

  /* front: person & contact */
  .person { position: absolute; left: 28px; bottom: 26px; }
  .person__name {
    color: var(--accent); font-weight: 800; font-size: 27px; line-height: 1.1;
  }
  .person__role { color: var(--ink); font-size: 14px; margin-bottom: 12px; }
  .person__tagline { color: var(--ink); font-size: 13.5px; margin-bottom: 12px; }
  .contact { list-style: none; }
  .contact__item {
    color: var(--ink); font-size: 13.5px; line-height: 1.45;
    display: flex; align-items: center; gap: 8px;
  }
  .contact__icon { width: 13px; height: 13px; flex: none; }

  /* back */
  .back-brand {
    position: absolute; left: 40px; top: 50%; transform: translateY(-50%);
    display: flex; align-items: center; gap: 26px;
  }
  .back-brand__name {
    color: var(--emboss); font-weight: 900; font-size: 58px;
    line-height: .92; text-transform: uppercase;
  }
  .back-brand__dot {
    width: 110px; height: 110px; border-radius: 50%;
    border: 10px solid #0a0a0a;
  }
</style>
</head>
<body>
<main class="stage">

  <section class="card card--front" aria-label="Card front">
    <div class="brand">
      <div class="brand__name">Flood<br>Rescue 360</div>
      <span class="brand__dot" aria-hidden="true"></span>
    </div>

    <div class="services">
      <h2 class="services__title">Services</h2>
      <ul class="services__list">
        <li class="services__item">Water</li>
        <li class="services__item">Fire</li>
        <li class="services__item">Mold</li>
        <li class="services__item">Reconstruction</li>
      </ul>
    </div>

    <div class="person">
      <h1 class="person__name">Marcus Pelley</h1>
      <p class="person__role">General Manager</p>
      <p class="person__tagline">Urgency for Your Water Emergency!</p>
      <ul class="contact">
        <li class="contact__item">
          <svg class="contact__icon" viewBox="0 0 14 14" aria-hidden="true"><rect x="3.5" y="1" width="7" height="12" rx="1.2" fill="none" stroke="var(--accent)" stroke-width="1.4"/><circle cx="7" cy="11" r=".8" fill="var(--accent)"/></svg>
          214-555-0193
        </li>
        <li class="contact__item">
          <svg class="contact__icon" viewBox="0 0 14 14" aria-hidden="true"><path d="M3 1.5l2.2 2.6-1.2 1.5c.8 1.8 2.2 3.2 4 4l1.5-1.2 2.6 2.2-1.3 1.9C6 12.3 1.7 8 1.2 2.8z" fill="var(--accent)"/></svg>
          469-555-0148
        </li>
        <li class="contact__item">
          <svg class="contact__icon" viewBox="0 0 14 14" aria-hidden="true"><rect x="1" y="3" width="12" height="8.5" rx="1" fill="var(--accent)"/><path d="M1.5 3.6L7 8l5.5-4.4" fill="none" stroke="var(--card)" stroke-width="1.2"/></svg>
          Marcus@FloodRescue360.example
        </li>
        <li class="contact__item">
          <svg class="contact__icon" viewBox="0 0 14 14" aria-hidden="true"><circle cx="7" cy="7" r="5.8" fill="none" stroke="var(--accent)" stroke-width="1.4"/><path d="M1.5 7h11M7 1.2c-2.4 3.2-2.4 8.4 0 11.6M7 1.2c2.4 3.2 2.4 8.4 0 11.6" fill="none" stroke="var(--accent)" stroke-width="1"/></svg>
          FloodRescue360.example
        </li>
      </ul>
    </div>
  </section>

  <section class="card card--back" aria-label="Card back">
    <div class="back-brand">
      <div class="back-brand__name">Flood<br>Rescue 360</div>
      <span class="back-brand__dot" aria-hidden="true"></span>
    </div>
  </section>

</main>
</body>
</html>
```